Client website

Our designer we were working with had some personal things come up and was unable to finish the design for the site.

We have a .psd file started, and will be attaching it to the project.
Updates

Reason: I still want to polish the designs with the current designer and allow more designers the opportunity to participate.

Reason: I'm extending the deadline for another day to give everyone enough time for the final changes our client wants.

I'm trying to extend the deadline so we can get one last set of comps in for my client.  Could everyone message me and let me know how much time they need to do the final tweaks?

Reason: Hey everyone.  I've been sick the last 3 days and I haven't been able to provide feedback on designs.  I'm extending just a few more days so I can catch up here.  Thanks everyone for your patience.

Target Market(s)

Adults in United States aged 25 to 60 that handle the household budgets and maintenance.

Requirements
Must have
• 1) We need 2 pages. 1 page for flood restoration, 1 page for carpet cleaning

2) The 1-800-# must be the focal point of the website for both pages. People are mostly looking to contact someone ASAP to get them out to their house when flooding occurs.

3) We''re going to have a slide show area to high-light different sub-services offered for each page.

4) We really want a chatterbook / plinker feed area. We''re going to use chatterbook for special offers, and plinker for weather updates. The chatterbook feed is going to be on the carpet cleaning page. The plinker feed is going to be on the flood page.

5) We want an SEO text sections near the bottom.

6) The very bottom will link to the privacy policy and user agreement as well as company name and copyright details.

We really want to stick to the say "theme" that our first designer started with.
Nice to have
• I'm not a designer, so if you think something looks better somewhere, or something can be eliminated, or something can be enhanced, but all means, let us know.

```html
<!DOCTYPE html>
<html lang="en">
<head>
<meta charset="utf-8">
<title>Pure-Nap Carpet Cleaning</title>
<link href="https://fonts.googleapis.com/css2?family=PT+Sans:wght@400;700&family=Reenie+Beanie&display=swap" rel="stylesheet">
<style>
:root{
  --backdrop:#1c2a36;
  --rail-blue:#1f8fdc;
  --carpet:#857b72;
  --carpet-dark:#6f665e;
  --panel:#ebe8e5;
  --panel-edge:#d7d3cf;
  --heading-blue:#2180c6;
  --body-grey:#6d6d6d;
  --nav-blue:#2b95d9;
  --nav-blue-dark:#1b74b8;
  --nav-green:#2fb33a;
  --nav-green-dark:#1c8c26;
  --brand-green:#1ea23a;
  --note:#efece0;
  --footer-text:#2b2b2b;
}
*{margin:0;padding:0;box-sizing:border-box}
html,body{width:1200px;height:1200px;overflow:hidden}
body{background:radial-gradient(ellipse at 50% 30%,#2a3c4b 0%,var(--backdrop) 75%);font-family:Arial,Helvetica,sans-serif;position:relative}
.site{position:absolute;left:135px;top:0;width:933px;height:1200px;border-left:5px solid var(--rail-blue);border-right:5px solid var(--rail-blue);background:linear-gradient(180deg,var(--carpet) 0%,var(--carpet-dark) 100%);overflow:visible}
.carpet-texture{position:absolute;inset:350px 0 0 0;background:linear-gradient(180deg,#968c83 0%,#7d736b 40%,#5f5750 100%)}
.hero-photo{position:absolute;left:0;top:0;width:923px;height:315px;background:linear-gradient(180deg,#a9a7a3 0%,#8e8c88 60%,#9c958c 80%,#8c847b 100%)}
.brand{position:absolute;left:48px;top:212px}
.brand-name{font-family:'PT Sans',sans-serif;font-weight:700;font-size:38px;color:var(--brand-green);letter-spacing:0.5px;line-height:1}
.brand-tag{font-family:'PT Sans',sans-serif;font-weight:400;font-size:13px;color:#333;letter-spacing:1px;margin-top:4px;margin-left:74px;font-variant:small-caps}
.main-nav{position:absolute;left:0;top:315px;display:flex;height:35px}
.main-nav a{display:block;width:147px;height:35px;line-height:38px;text-align:center;font-family:'PT Sans',sans-serif;font-size:17px;letter-spacing:1px;color:#fff;text-decoration:none;background:linear-gradient(180deg,#56b3ec 0%,var(--nav-blue) 50%,var(--nav-blue-dark) 100%);border-right:1px solid #8cc9f0}
.main-nav a.active{background:linear-gradient(180deg,#5fd067 0%,var(--nav-green) 50%,var(--nav-green-dark) 100%)}
.main-nav .tail{width:70px;height:35px;background:linear-gradient(180deg,#56b3ec,var(--nav-blue-dark))}
.call-note{position:absolute;left:760px;top:190px;width:240px;height:175px;background:var(--note);transform:rotate(21deg);box-shadow:4px 6px 10px rgba(0,0,0,.35);font-family:'Reenie Beanie',cursive;color:#333;padding:26px 18px;line-height:1}
.call-note .ask{font-size:40px;display:block;margin-left:22px}
.call-note .number{font-size:34px;display:block;margin-top:8px}
.pin{position:absolute;left:810px;top:160px;width:20px;height:20px;border-radius:50%;background:#3fcf3a}
.panel{position:absolute;background:var(--panel);border-radius:12px;box-shadow:0 2px 4px rgba(0,0,0,.35)}
.slider{left:38px;top:395px;width:844px;height:297px;border-radius:16px}
.slider h1{position:absolute;left:44px;top:40px;font-family:'PT Sans',sans-serif;font-weight:700;font-size:48px;letter-spacing:-1.5px;color:var(--heading-blue)}
.slider .copy{position:absolute;left:48px;top:130px;width:510px;font-size:16px;line-height:18px;color:var(--body-grey)}
.slider .copy p+p{margin-top:18px}
.cta{position:absolute;left:614px;top:172px;width:177px;height:43px;border-radius:8px;background:linear-gradient(180deg,#5ee35a 0%,#25b12e 55%,#129a1e 100%);color:#fff;font-family:'PT Sans',sans-serif;font-weight:700;font-size:22px;text-align:center;line-height:43px;box-shadow:0 2px 3px rgba(0,0,0,.3)}
.arrow{position:absolute;top:522px;width:44px;height:44px;border-radius:50%;background:radial-gradient(circle at 50% 30%,#6cc6f7,#1479c9);border:2px solid #fff;box-shadow:0 2px 4px rgba(0,0,0,.4)}
.arrow.prev{left:15px}.arrow.next{left:859px}
.feed{width:400px;height:172px}
.feed.chatter{left:38px;top:733px}
.feed.plinker{left:481px;top:736px}
.feed .icon{position:absolute;left:44px;top:40px;width:64px;height:64px;border-radius:6px;background:linear-gradient(180deg,#d9dfe8,#aab6c8);box-shadow:0 1px 3px rgba(0,0,0,.35)}
.feed .follow{position:absolute;left:36px;top:112px;width:80px;height:22px;background:linear-gradient(180deg,#fff,#ddd);border:1px solid #bbb;font-size:12px;line-height:20px;text-align:center;color:#222}
.feed h2{position:absolute;left:142px;top:28px;font-family:'PT Sans',sans-serif;font-weight:700;font-size:30px;letter-spacing:-1px;color:var(--heading-blue)}
.feed p{position:absolute;left:142px;top:70px;width:245px;font-size:13px;line-height:15px;color:var(--body-grey)}
.seo{top:954px;width:262px;height:92px;border-radius:4px}
.seo p{padding:16px 28px;font-size:11px;line-height:15px;color:#7a7a7a}
.seo.first{left:38px}.seo.second{left:330px}.seo.third{left:619px}
.site-footer{left:38px;top:1091px;width:844px;height:36px;border-radius:4px;display:flex;justify-content:space-between;align-items:center;padding:0 38px 0 28px;font-size:11px;color:var(--footer-text)}
.site-footer a{color:var(--footer-text);text-decoration:none}
</style>
</head>
<body>
<div class="site">
  <div class="carpet-texture" role="img" aria-label="Close-up texture of brown carpet pile"></div>
  <div class="hero-photo" role="img" aria-label="Photo of a modern room with a concrete wall, an armchair and an upright vacuum cleaner on carpet"></div>

  <div class="brand">
    <div class="brand-name">PURE-NAP</div>
    <div class="brand-tag">Carpet Cleaning</div>
  </div>

  <nav class="main-nav">
    <a class="active" href="#">home</a>
    <a href="#">about</a>
    <a href="#">services</a>
    <a href="#">faq</a>
    <a href="#">contact</a>
    <span class="tail"></span>
  </nav>

  <section class="panel slider">
    <h1>Sub-service Number One</h1>
    <div class="copy">
      <p>Lorem ipsum dolor sit amet, consectetur adipiscing elit. Duis semper, turpis in sodales ultricies, felis dui facilisis sem, nec dignissim augue nisl eu eros. Sed a faucibus massa.</p>
      <p>Suspendisse id felis tellus, vel sagittis sem. Fusce aliquam scelerisque diam et tempor.</p>
    </div>
    <a class="cta">A Button »</a>
  </section>
  <svg class="arrow prev" viewBox="0 0 44 44"><path d="M22 14l-8 8 8 8M30 14l-8 8 8 8" fill="none" stroke="#fff" stroke-width="3"/></svg>
  <svg class="arrow next" viewBox="0 0 44 44"><path d="M14 14l8 8-8 8M22 14l8 8-8 8" fill="none" stroke="#fff" stroke-width="3"/></svg>

  <section class="panel feed chatter">
    <div class="icon"></div>
    <div class="follow">Follow us!</div>
    <h2>Chatterbook Feed</h2>
    <p>- Lorem ipsum dolor sit amet, consectetur adipiscing elit. Duis semper, turpis in sodales ultricies, felis dui facilisis sem, nec dignissim</p>
  </section>
  <section class="panel feed plinker">
    <div class="icon"></div>
    <div class="follow">Follow us!</div>
    <h2>Plinker Feed</h2>
    <p>- Lorem ipsum dolor sit amet, consectetur adipiscing elit. Duis semper, turpis in sodales ultricies, felis dui facilisis sem, nec dignissim</p>
  </section>

  <section class="panel seo first"><p>- Lorem ipsum dolor sit amet, consectetur adipiscing elit. Duis semper, turpis in sodales ultricies, felis dui facilisis sem, nec dignissim</p></section>
  <section class="panel seo second"><p>- Lorem ipsum dolor sit amet, consectetur adipiscing elit. Duis semper, turpis in sodales ultricies, felis dui facilisis sem, nec dignissim</p></section>
  <section class="panel seo third"><p>- Lorem ipsum dolor sit amet, consectetur adipiscing elit. Duis semper, turpis in sodales ultricies, felis dui facilisis sem, nec dignissim</p></section>

  <footer class="panel site-footer">
    <span>Copyright 2010. Pure-Nap.</span>
    <span><a href="#">Privacy Policy</a> | <a href="#">User Agreement</a></span>
  </footer>

  <div class="call-note">
    <span class="ask">Call Us Now!</span>
    <span class="number">1-800-555-0142!</span>
  </div>
  <div class="pin"></div>
</div>
</body>
</html>
```